Flyer for tutoring

The text should be presented in an engaging way to attract potential customers.
Colorfully designed
Around the edge, various objects related to school and the subjects (see text) should be visible.

```html
<!DOCTYPE html>
<html lang="de">
<head>
<meta charset="utf-8">
<title>Lerncoach Flyer</title>
<link rel="stylesheet" href="https://fonts.googleapis.com/css2?family=Barlow+Semi+Condensed:wght@600;700;800&family=Rubik:wght@400&family=Open+Sans:wght@400&display=swap">
<style>
  :root {
    --page-bg: #e9e9e9;
    --paper: #ffffff;
    --yellow-light: #fdf08a;
    --yellow-deep: #f3e114;
    --bubble-shadow: #4f5052;
    --ink: #111111;
    --text: #222222;
    --grey-text: #555555;
    --orange: #e55622;
    --blue: #3a62b0;
    --rule: #cfcfcf;
  }
  * { margin: 0; padding: 0; box-sizing: border-box; }
  html, body { width: 801px; height: 1200px; overflow: hidden; background: var(--page-bg); }
  .flyer {
    position: absolute; left: 10px; top: 47px;
    width: 780px; height: 1106px;
    background: var(--paper); overflow: hidden;
    font-family: "Open Sans", sans-serif; color: var(--text);
  }
  .flyer-shapes { position: absolute; left: 0; top: 0; width: 780px; height: 1106px; }
  .headline-line {
    position: absolute; white-space: nowrap; line-height: 1;
    transform-origin: 0 80%; transform: rotate(-7.4deg);
  }
  .headline-question { font-family: "Rubik", sans-serif; font-size: 30px; color: var(--grey-text); letter-spacing: 0.5px; }
  .headline-accent { font-family: "Rubik", sans-serif; font-size: 68px; color: var(--orange); }
  .headline-main { font-family: "Barlow Semi Condensed", sans-serif; font-weight: 800; font-size: 122px; color: var(--ink); letter-spacing: 1px; }
  .photo-area {
    position: absolute; left: 468px; top: 321px; width: 312px; height: 377px;
    background: radial-gradient(ellipse at 65% 65%, rgba(226,52,40,0.55), rgba(250,230,60,0) 65%);
  }
  .intro-title {
    position: absolute; left: 53px; top: 392px;
    font-family: "Barlow Semi Condensed", sans-serif; font-weight: 700;
    font-size: 29px; line-height: 28px; color: var(--ink);
  }
  .intro-text {
    position: absolute; left: 53px; font-size: 17.4px; line-height: 22.4px; color: var(--text);
  }
  .intro-text.first { top: 459px; }
  .intro-text.second { top: 635px; }
  .promise-banner {
    position: absolute; left: 53px; top: 699px; width: 674px; height: 102px;
    background: var(--blue); border-radius: 6px;
    box-shadow: 0 12px 10px -6px rgba(0,0,0,0.35);
  }
  .promise-banner::before {
    content: ""; position: absolute; inset: 4px;
    border: 2px dashed rgba(255,255,255,0.85); border-radius: 3px;
  }
  .promise-text {
    position: absolute; inset: 0; display: flex; flex-direction: column; justify-content: center; align-items: center;
    font-family: "Barlow Semi Condensed", sans-serif; font-weight: 700;
    font-size: 37px; line-height: 36px; color: var(--paper); text-align: center;
  }
  .about-badge {
    position: absolute; left: 57px; top: 826px; width: 94px; height: 94px; border-radius: 50%;
    background: var(--ink); color: var(--paper);
    display: flex; align-items: center; justify-content: center; text-align: center;
    font-family: "Barlow Semi Condensed", sans-serif; font-weight: 700; font-size: 23px; line-height: 20px;
  }
  .about-text { position: absolute; left: 178px; top: 826px; font-size: 17.4px; line-height: 22.4px; }
  .contact-rule { position: absolute; left: 53px; top: 948px; width: 674px; height: 1px; background: var(--rule); }
  .contact-icon { position: absolute; top: 976px; width: 35px; height: 35px; }
  .contact-icon.phone { left: 53px; }
  .contact-icon.mail { left: 397px; }
  .contact-phone {
    position: absolute; left: 101px; top: 970px;
    font-family: "Barlow Semi Condensed", sans-serif; font-weight: 800; font-size: 33px; line-height: 36px; color: var(--ink);
  }
  .contact-note { position: absolute; left: 101px; top: 1005px; font-size: 12px; color: var(--grey-text); }
  .contact-mail { position: absolute; left: 444px; top: 978px; font-size: 22px; line-height: 30px; color: var(--ink); }
  .footer-band {
    position: absolute; left: 0; top: 1038px; width: 780px; height: 68px; background: var(--orange);
    display: flex; align-items: center; justify-content: center;
    color: var(--paper); font-size: 22px;
  }
</style>
</head>
<body>
<main class="flyer">
  <svg class="flyer-shapes" viewBox="0 0 1146 1625" aria-hidden="true">
    <defs>
      <linearGradient id="yellowField" x1="0" y1="1" x2="1" y2="0">
        <stop offset="0" stop-color="var(--yellow-deep)"/>
        <stop offset="0.6" stop-color="var(--yellow-light)"/>
        <stop offset="1" stop-color="var(--yellow-deep)"/>
      </linearGradient>
    </defs>
    <rect class="yellow-field" x="0" y="0" width="1146" height="1082" fill="url(#yellowField)"/>
    <path class="bubble-shadow" fill="var(--bubble-shadow)"
      d="M0 24 H1037 L1084 364 Q1088 400 1052 410 L912 435 L934 624 L629 477 L0 545 Z"/>
    <path class="speech-bubble" fill="var(--paper)"
      d="M0 0 H1037 L1084 340 Q1088 374 1052 384 L912 410 L905 598 L629 453 L0 521 Z"/>
  </svg>

  <div class="headline-line headline-question" style="left:44px; top:96px;">Möchtest du dich gerne in der</div>
  <div class="headline-line headline-question" style="left:47px; top:132px;">Schule verbessern und suchst eine</div>
  <div class="headline-line headline-accent" style="left:56px; top:170px;">Professionelle</div>
  <div class="headline-line headline-main" style="left:68px; top:216px;">LERNCOACH?</div>

  <div class="photo-area" role="img" aria-label="Foto eines fröhlichen Kindes im roten T-Shirt mit einem Bücherstapel, umgeben von bunten Schul-Kritzeleien"></div>

  <h2 class="intro-title">Dann lass es uns doch<br>mal versuchen!</h2>
  <p class="intro-text first">Die erste Lektion – die Kennenlernlektion –<br>dauert ca. 30 Minuten. Sie ist kostenlos.<br>Denn wir müssen ja sicher gehen, dass wir<br>uns verstehen und leiden können. Bei<br>unserem ersten Treffen legen wir auch fest,<br>woran wir arbeiten werden und wann die<br>Nachhilfe in deine Agenda passt.</p>
  <p class="intro-text second">Wenn der erste Eindruck stimmt, dann legen<br>wir los, und bald schon werden</p>

  <div class="promise-banner">
    <p class="promise-text"><span>DEINE MOTIVATION UND</span><span>DEINE NOTEN BESSER UND BESSER!</span></p>
  </div>

  <div class="about-badge">Zu<br>meiner<br>Person</div>
  <p class="about-text">Ich wohne hier in der Wohnsiedlung Lindenweg und bin<br>ausgebildete und sehr erfahrene Sekundar- und Primarlehrerin<br>in den Fächern Deutsch, Französisch, Englisch und Geschichte.<br>(Auf Wunsch auch Mathe-Nachhilfe möglich.)</p>

  <div class="contact-rule"></div>

  <svg class="contact-icon phone" viewBox="0 0 36 36" aria-hidden="true">
    <circle cx="18" cy="18" r="17" fill="var(--orange)"/>
    <path d="M12 9 l4 0 l1.5 5 l-2.5 2 q2 4 5 5 l2 -2.5 l5 1.5 l0 4 q-1 2 -4 2 q-12 -3 -13 -13 q0 -3 2 -4 z" fill="var(--paper)"/>
  </svg>
  <div class="contact-phone">079 123 45 67</div>
  <div class="contact-note">(nachmittags fast immer erreichbar)</div>

  <svg class="contact-icon mail" viewBox="0 0 36 36" aria-hidden="true">
    <circle cx="18" cy="18" r="17" fill="var(--orange)"/>
    <rect x="9" y="12" width="18" height="12" rx="1" fill="none" stroke="var(--paper)" stroke-width="2"/>
    <path d="M9 12 L18 19 L27 12" fill="none" stroke="var(--paper)" stroke-width="2"/>
  </svg>
  <div class="contact-mail">kontakt@lernzeit-coach.ch</div>

  <footer class="footer-band">Ich freue mich auf deine Kontaktaufnahme! Bis bald!</footer>
</main>
</body>
</html>
```